Voucher design for Silver Brook Spa

1) Create a creative design and voucher for Silver Brook Spa that create a lasting memory for the audience. I would like to give out vouchers to all neighbours.
2) Kindly look at the website www.silverbrookspa.example
3) Content must include logo, address, telephone number and website.

Here is the content of the voucher

2) 15 dollar cash voucher - off full body massage
3) 10 dollars cash voucher - off foot massage
(Both the fully body massage and foot massage, slimming massage vouchers must be separated and separate vouchers and independent)
4) 20 dollars cash voucher - off slimming massage

Terms and conditions at the back of the voucher
1) Silver Brook Spa reserved the right to amend change the terms and conditions without prior notice.
2) This promotional is not valid with any other promotions existing. e.g
3) Each person is entitled to use one voucher at any one time.

Target Market(s)

Mass market

Font styles to use
Decorative

Requirements
Must have
• 1) Creatives cash vouchers and beautiful design
• 2) Logo fo the company
• 3) Address and telephone number
• 4) website
• 5) Terms and conditions
Nice to have
• You can use tree or lotus as the symbol but it must be toward nature, beautiful, eye catching and creative.

```html
<!DOCTYPE html>
<html lang="en">
<head>
<meta charset="utf-8">
<title>Silver Brook Spa – Cash Voucher</title>
<link href="https://fonts.googleapis.com/css2?family=Montserrat:wght@300;400;500;600;700;800&display=swap" rel="stylesheet">
<style>
  :root{
    --canvas:#dedddd;
    --black:#000;
    --gold:#f5b82e;
    --cream:#f6efc4;
    --badge:#fbf3b8;
    --badge-ring:#2a1a10;
    --badge-outer:#f4de7a;
    --red:#c1272d;
    --white:#fff;
    --paper:#fff;
    --ink:#333;
    --rule:#bdbdbd;
    --logo:#2f5ea8;
  }
  *{margin:0;padding:0;box-sizing:border-box}
  html,body{width:1200px;height:960px;overflow:hidden}
  body{background:var(--canvas);font-family:'Montserrat',sans-serif;position:relative}

  .voucher-front{position:absolute;left:21px;width:576px;height:440px;overflow:hidden;background:var(--black)}
  .voucher-front.top{top:24px}
  .voucher-front.bottom{top:470px;background:linear-gradient(160deg,#0d1230 0%,#070a1a 55%,#020207 100%)}

  .brand-mark{position:absolute;left:37px;top:30px;width:180px;display:flex;flex-direction:column;align-items:center;gap:12px}
  .brand-mark .dot{width:64px;height:64px;border-radius:50%;background:#2a8f4a}
  .brand-mark .name{font-weight:700;font-size:20px;letter-spacing:1px;color:var(--logo);white-space:nowrap}

  .hero-photo{position:absolute;left:300px;top:0;width:276px;height:190px}

  .price-badge{position:absolute;left:430px;top:110px;width:128px;height:128px;border-radius:50%;background:var(--badge);
    border:3px solid var(--badge-ring);box-shadow:0 0 0 5px var(--badge-outer);text-align:center;padding-top:22px}
  .price-badge .amount{font-weight:800;font-size:29px;color:#1c120b;line-height:1}
  .price-badge .kind{font-weight:700;font-size:11.5px;color:#1c120b;margin-top:5px}
  .price-badge .off{font-weight:700;font-size:8.5px;color:#1c120b;margin-top:1px}
  .price-badge .what{font-weight:600;font-size:8.5px;color:var(--red);margin-top:1px}

  .spa-title{position:absolute;left:40px;top:180px;font-weight:400;font-size:37px;letter-spacing:.3px;color:var(--gold);line-height:1;white-space:nowrap}
  .spa-tagline{position:absolute;left:40px;top:221px;font-weight:400;font-size:25.5px;letter-spacing:.8px;color:var(--white);line-height:1;white-space:nowrap}
  .spa-address{position:absolute;left:45px;top:287px;font-weight:700;font-size:16px;line-height:18px;letter-spacing:.5px;color:var(--cream)}
  .spa-phone{position:absolute;left:40px;top:340px;font-weight:700;font-size:31px;line-height:1;letter-spacing:1px;color:var(--white)}
  .spa-web{position:absolute;left:178px;top:400px;font-weight:700;font-size:17px;line-height:1;letter-spacing:.5px;color:var(--white)}

  .flower-glow{position:absolute;left:300px;top:250px;width:276px;height:190px;
    background:radial-gradient(ellipse at 55% 50%,rgba(150,20,30,.55) 0%,rgba(90,10,20,.3) 40%,rgba(0,0,0,0) 70%)}

  .voucher-back{position:absolute;left:603px;top:190px;width:576px;height:440px;background:var(--paper);color:var(--ink)}
  .voucher-back .divider{position:absolute;left:278px;top:0;width:1px;height:440px;background:var(--rule)}
  .back-brand{position:absolute;left:22px;top:16px;display:flex;flex-direction:column;align-items:center;gap:8px;width:90px}
  .back-brand .dot{width:36px;height:36px;border-radius:50%;background:#5aa84f}
  .back-brand .name{font-weight:600;font-size:11px;color:var(--logo);white-space:nowrap}
  .terms-heading{position:absolute;left:25px;top:106px;font-weight:700;font-size:9px}
  .terms-list{position:absolute;left:28px;top:131px;width:222px;list-style:none;font-size:9px;line-height:11px;font-weight:400}
  .terms-list li{position:relative;padding-left:14px;margin-bottom:10px}
  .terms-list li::before{content:"•";position:absolute;left:0}
  .spa-still{position:absolute;left:0;top:282px;width:133px;height:158px}
  .return-address{position:absolute;right:322px;top:302px;text-align:right;font-size:8.8px;line-height:11px;white-space:nowrap}
  .return-address .label{font-weight:700;margin-bottom:10px}
  .return-address p+p{margin-top:10px}
  .stamp-box{position:absolute;left:462px;top:31px;width:86px;height:86px;border:1px solid var(--rule)}
  .address-lines{position:absolute;left:309px;top:225px;width:196px}
  .address-lines span{display:block;height:1px;background:var(--rule);margin-bottom:21px}
</style>
</head>
<body>

<section class="voucher-front top">
  <div class="brand-mark"><span class="dot"></span><span class="name">SILVER BROOK</span></div>
  <svg class="hero-photo" viewBox="0 0 276 190" role="img" aria-label="Photo of a couple relaxing during a spa massage with candles">
    <defs><linearGradient id="warm1" x1="0" y1="0" x2="1" y2="1"><stop offset="0" stop-color="#f3e6da"/><stop offset=".5" stop-color="#d9a98a"/><stop offset="1" stop-color="#8a5a3e"/></linearGradient></defs>
    <path d="M22 0 Q-8 115 90 165 Q150 192 276 178 L276 0 Z" fill="url(#warm1)" stroke="#8d8d8d" stroke-width="4"/>
  </svg>
  <div class="price-badge"><div class="amount">$15</div><div class="kind">CASH VOUCHER</div><div class="off">OFF 1 HOUR</div><div class="what">FULL BODY MASSAGE</div></div>
  <h1 class="spa-title">SILVER BROOK SPA</h1>
  <p class="spa-tagline">MEDITATION &amp; MASSAGE</p>
  <p class="spa-address">12 Harbour Lane #02-14<br>Singapore - 400123</p>
  <p class="spa-phone">+65 6000 1234</p>
  <p class="spa-web">www.silverbrookspa.example</p>
</section>

<section class="voucher-front bottom">
  <div class="flower-glow" role="img" aria-label="Faint red flower reflected on dark water"></div>
  <div class="brand-mark"><span class="dot"></span><span class="name">SILVER BROOK</span></div>
  <svg class="hero-photo" viewBox="0 0 276 190" role="img" aria-label="Photo of a couple relaxing during a spa massage with candles">
    <defs><linearGradient id="warm2" x1="0" y1="0" x2="1" y2="1"><stop offset="0" stop-color="#f3e6da"/><stop offset=".5" stop-color="#d9a98a"/><stop offset="1" stop-color="#8a5a3e"/></linearGradient></defs>
    <path d="M22 0 Q-8 115 90 165 Q150 192 276 178 L276 0 Z" fill="url(#warm2)" stroke="#8d8d8d" stroke-width="4"/>
  </svg>
  <div class="price-badge"><div class="amount">$15</div><div class="kind">CASH VOUCHER</div><div class="off">OFF 1 HOUR</div><div class="what">FULL BODY MASSAGE</div></div>
  <h1 class="spa-title">SILVER BROOK SPA</h1>
  <p class="spa-tagline">MEDITATION &amp; MASSAGE</p>
  <p class="spa-address">12 Harbour Lane #02-14<br>Singapore - 400123</p>
  <p class="spa-phone">+65 6000 1234</p>
  <p class="spa-web">www.silverbrookspa.example</p>
</section>

<section class="voucher-back">
  <div class="back-brand"><span class="dot"></span><span class="name">SILVER BROOK</span></div>
  <h2 class="terms-heading">Terms and conditions</h2>
  <ul class="terms-list">
    <li>Silver Brook Spa reserved the right to amend change the terms and conditions without prior notice.</li>
    <li>This promotional is not valid with any other promotions.</li>
    <li>Each person is entitled to use one voucher at any one time.</li>
    <li>The validity of this voucher is until ...............</li>
  </ul>
  <div class="spa-still" role="img" aria-label="Pink orchid in a white pot beside rolled white towels" style="background:linear-gradient(160deg,#f7f2f5 0%,#e7c4d8 35%,#cfd9c2 65%,#eeeeee 100%)"></div>
  <div class="return-address">
    <p class="label">Return Address:</p>
    <p>12 Harbour Lane #02-14<br>Singapore - 400123</p>
    <p>Phone: +65 6000 1234<br>Email: hello@silverbrookspa.example</p>
  </div>
  <span class="divider"></span>
  <div class="stamp-box"></div>
  <div class="address-lines"><span></span><span></span><span></span><span></span></div>
</section>

</body>
</html>
```